Laser Tattoo Removal Business Cards

We are looking for a professional business card design for a laser tattoo removal business. Ideally looking for a black business card design. The name of the business is Brightline Tattoo Removal. We place our cards at local tattoo shops so we ideally are looking for something trendy/edgy to draw both male and female clientele in.

Target Market(s)

Male/Female ages 18-60

Contact Information for Business Card

black background ideally.. hoping to stay within greys, whites and black

Font styles to use
Serif
Sans Serif

Colors
121212
a9a9a9
5c5c5c
f5f5f5
ffffff
7f7f7f
606060
848484
9d9d9d

Requirements
Must have
• Employee Info:
• Melissa Thornbury
• Chief Executive Offer
• m: 919.537.2846
• w: 919.362.4178
• f: 919.685.3907
• mthornbury@brightlinetattooremoval.example
• Address:
• 4615 Oakmere Pkwy, Suite 210
• Raleigh, NC 27654
• Website:
• www.brightlinetattooremoval.example
Nice to have
• Myabe business name on back or logo on back and employee info on the front

```html
<!DOCTYPE html>
<html lang="en">
<head>
<meta charset="utf-8">
<title>Brightline Tattoo Removal – Business Cards</title>
<link rel="stylesheet" href="https://fonts.googleapis.com/css2?family=Oswald:wght@300;400;500&family=Open+Sans:wght@400;600;700&display=swap">
<style>
  :root {
    --ink: #121212;
    --grey-light: #a9a9a9;
    --grey-dark: #5c5c5c;
    --paper: #f5f5f5;
    --white: #ffffff;
    --grey-mid: #7f7f7f;
    --grey-text: #606060;
    --grey-soft: #848484;
    --grey-pale: #9d9d9d;
    --stage-left: #d4d4d4;
    --stage-right: #8a8a8a;
  }
  * { margin: 0; padding: 0; box-sizing: border-box; }
  html, body { width: 1200px; height: 960px; overflow: hidden; }
  body {
    position: relative;
    background: linear-gradient(90deg, var(--stage-left) 0%, var(--stage-right) 100%);
    font-family: "Open Sans", Arial, sans-serif;
  }

  /* Front card */
  .card-front {
    position: absolute;
    left: 302px; top: 122px;
    width: 600px; height: 343px;
    overflow: hidden;
    background: var(--white);
  }
  .card-front__texture {
    position: absolute; inset: 0;
    background: radial-gradient(ellipse at 50% 45%, var(--white) 0%, #f7f7f7 55%, #f0f0f0 100%);
  }
  .card-front__band {
    position: absolute; left: 0; bottom: 0;
    width: 600px; height: 11px;
  }
  .holder-name {
    position: absolute; left: 0; right: 7px; top: 196px;
    top: 74px;
    text-align: center;
    font-family: "Oswald", "Arial Narrow", sans-serif;
    font-weight: 400;
    font-size: 36px; line-height: 40px;
    letter-spacing: 0.5px;
    color: var(--ink);
    transform: scaleY(1.05);
  }
  .holder-email {
    position: absolute; left: 0; right: 14px; top: 115px;
    text-align: center;
    font-family: "Oswald", "Arial Narrow", sans-serif;
    font-weight: 300;
    font-size: 12.5px; line-height: 16px;
    color: var(--grey-pale);
  }
  .holder-title {
    position: absolute; left: 0; right: 18px; top: 133px;
    text-align: center;
    font-weight: 600;
    font-size: 13px; line-height: 16px;
    letter-spacing: 0.3px;
    color: var(--grey-mid);
  }
  .contact-phones {
    position: absolute; right: 322px; top: 174px;
    text-align: right;
    list-style: none;
    font-size: 13.5px; line-height: 18px;
    color: var(--grey-dark);
  }
  .contact-divider {
    position: absolute; left: 295px; top: 175px;
    width: 1px; height: 52px;
    background: var(--grey-dark);
  }
  .contact-address {
    position: absolute; left: 312px; top: 174px;
    font-style: normal;
    font-size: 13.5px; line-height: 18px;
    color: var(--grey-dark);
  }
  .holder-web {
    position: absolute; left: 0; right: 0; top: 253px;
    text-align: center;
    font-size: 13.5px; line-height: 18px;
    letter-spacing: 0.8px;
    color: var(--grey-dark);
  }
  .holder-web strong { font-weight: 700; color: var(--grey-dark); }

  /* Back card */
  .card-back {
    position: absolute;
    left: 299px; top: 495px;
    width: 600px; height: 343px;
    background: #1b1b1c;
  }
  .card-back__frame {
    position: absolute; left: 10px; top: 10px;
    width: 580px; height: 322px;
    border: 1px solid var(--grey-soft);
  }
  .brand-name {
    position: absolute; left: 0; right: 0; top: 100px;
    text-align: center;
    font-family: "Oswald", "Arial Narrow", sans-serif;
    font-weight: 400;
    color: var(--paper);
    letter-spacing: 4px;
  }
  .brand-name__main { display: block; font-size: 48px; line-height: 60px; }
  .brand-name__sub { display: block; font-size: 20px; line-height: 40px; letter-spacing: 5px; margin-top: 36px; }
</style>
</head>
<body>

<section class="card-front" aria-label="Business card front">
  <div class="card-front__texture" role="img" aria-label="Soft light grey damask pattern background"></div>

  <h1 class="holder-name">MELISSA THORNBURY</h1>
  <p class="holder-email">MTHORNBURY@BRIGHTLINETATTOOREMOVAL.EXAMPLE</p>
  <p class="holder-title">CHIEF EXECUTIVE OFFER</p>

  <ul class="contact-phones">
    <li>(m) 919.537.2846</li>
    <li>(w) 919.362.4178</li>
    <li>(f) 919.685.3907</li>
  </ul>
  <span class="contact-divider"></span>
  <address class="contact-address">
    4615 Oakmere Pkwy<br>
    Suite 210<br>
    Raleigh, NC 27654
  </address>

  <p class="holder-web">www.<strong>BRIGHTLINETATTOOREMOVAL</strong>.example</p>

  <svg class="card-front__band" viewBox="0 0 600 11" aria-hidden="true">
    <polygon points="0,0 392,0 388,11 0,11" fill="#1e1e1e"/>
    <polygon points="395,0 600,0 600,11 391,11" fill="#d8d8d8"/>
  </svg>
</section>

<section class="card-back" aria-label="Business card back">
  <div class="card-back__frame"></div>
  <p class="brand-name">
    <span class="brand-name__main">BRIGHTLINE</span>
    <span class="brand-name__sub">— TATTOO REMOVAL —</span>
  </p>
</section>

</body>
</html>
```